Telecommunications/Power civil contractor needs business card design

Were a new telecommunications/power underground civil contractor that is looking for a new business card design. Our company colours are silver or grey and orange. Feel free to use the white background logo or the black background logo.

Target Market(s)

Local contractors, utility companies, private sector mining/energy companies, developers.

Industry/Entity Type

Telecommunications

Contact Information for Business Card

Each card will need the following info:
Persons name:
Title:
E-mail:
Phone number:
Shop Address:
Mailing Address:

Requirements
Must have
• Each card will need the following info:
• Persons name:
• Title:
• E-mail:
• Phone number:
• Shop Address:
• Mailing Address:

```html
<!DOCTYPE html>
<html lang="en">
<head>
<meta charset="utf-8">
<title>Harlow Line Civil Inc — Business Card</title>
<link rel="stylesheet" href="https://fonts.googleapis.com/css2?family=Open+Sans:wght@400;600;700&display=swap">
<style>
  :root {
    --backdrop: #e9e6e2;
    --card-white: #ffffff;
    --card-black: #141414;
    --brand-orange: #f0541e;
    --brand-grey: #8a8a8a;
    --text-dark: #3a3a3a;
    --shadow: rgba(0, 0, 0, 0.22);
  }
  * { box-sizing: border-box; margin: 0; padding: 0; }
  html, body {
    width: 1200px;
    height: 675px;
    overflow: hidden;
    background: var(--backdrop);
    font-family: "Open Sans", Arial, sans-serif;
  }
  .canvas {
    position: relative;
    width: 1200px;
    height: 675px;
  }
  .card {
    position: absolute;
    top: 195px;
    width: 500px;
    height: 286px;
    border-radius: 18px;
    overflow: hidden;
    box-shadow: 0 10px 24px var(--shadow);
  }
  .card--back {
    left: 60px;
    background: var(--card-black);
    display: flex;
    align-items: center;
    justify-content: center;
  }
  .card--front {
    left: 640px;
    background: var(--card-white);
  }
  .wordmark {
    display: flex;
    align-items: center;
    gap: 12px;
  }
  .wordmark__dot {
    width: 34px;
    height: 34px;
    border-radius: 50%;
    background: var(--brand-orange);
    flex: none;
  }
  .wordmark__name {
    color: var(--brand-orange);
    font-weight: 700;
    font-size: 28px;
    line-height: 1.05;
    letter-spacing: 0.5px;
    text-transform: uppercase;
  }
  .card--front .wordmark {
    position: absolute;
    left: 28px;
    top: 32px;
  }
  .card--front .wordmark__name { font-size: 20px; }
  .card--front .wordmark__dot { width: 28px; height: 28px; }
  .swoosh {
    position: absolute;
    left: 0;
    top: 0;
    width: 500px;
    height: 286px;
  }
  .person {
    position: absolute;
    left: 40px;
    top: 168px;
    font-size: 13px;
    line-height: 1.4;
    color: var(--text-dark);
  }
  .person__name {
    color: var(--brand-orange);
    font-weight: 700;
  }
  .contact {
    position: absolute;
    left: 220px;
    top: 188px;
    font-size: 12.5px;
    line-height: 1.5;
    color: var(--text-dark);
    list-style: none;
  }
  .contact__item {
    display: flex;
    align-items: center;
    gap: 6px;
    white-space: nowrap;
  }
  .contact__icon {
    width: 12px;
    height: 12px;
    flex: none;
    fill: var(--brand-orange);
  }
</style>
</head>
<body>
<main class="canvas">
  <section class="card card--back" aria-label="Card back">
    <div class="wordmark">
      <span class="wordmark__dot"></span>
      <span class="wordmark__name">Harlow Line<br>Civil Inc</span>
    </div>
  </section>

  <section class="card card--front" aria-label="Card front">
    <svg class="swoosh" viewBox="0 0 500 286" aria-hidden="true">
      <path d="M0,100 C100,130 200,160 300,158 C400,156 460,185 500,225 L500,240 C455,198 395,168 300,166 C200,168 100,140 0,108 Z" fill="var(--brand-orange)"/>
      <path d="M300,170 C390,172 450,200 500,258 L500,280 C445,215 385,180 300,170 Z" fill="var(--brand-grey)"/>
    </svg>

    <div class="wordmark">
      <span class="wordmark__dot"></span>
      <span class="wordmark__name">Harlow Line<br>Civil Inc</span>
    </div>

    <div class="person">
      <p class="person__name">Corwin Hale</p>
      <p class="person__title">Managing Director</p>
    </div>

    <ul class="contact">
      <li class="contact__item">12 Ridge Avenue,</li>
      <li class="contact__item">Suite 200, Kestrel, WA 55555</li>
      <li class="contact__item">
        <svg class="contact__icon" viewBox="0 0 12 12" aria-hidden="true"><path d="M2.5 0.5 L4.5 0.5 L5.2 3 L3.8 4.2 C4.5 5.8 6.2 7.5 7.8 8.2 L9 6.8 L11.5 7.5 L11.5 9.5 C11.5 10.6 10.6 11.5 9.5 11.5 C4.5 11.5 0.5 7.5 0.5 2.5 C0.5 1.4 1.4 0.5 2.5 0.5 Z"/></svg>
        <span>555.014.229</span>
      </li>
      <li class="contact__item">
        <svg class="contact__icon" viewBox="0 0 12 12" aria-hidden="true"><path d="M0.5 2.5 H11.5 V3.2 L6 7 L0.5 3.2 Z M0.5 4.6 L6 8.4 L11.5 4.6 V10 H0.5 Z"/></svg>
        <span>info@harlowlinecivil.com</span>
      </li>
    </ul>
  </section>
</main>
</body>
</html>
```